Tech Savy small Business accountant business card design

We need a business card for a new company based in the cloud. We provide tax, business advisory, accounting, information technology solutions and back office functions to small businesses. We offer fixed fee packages with add on services as you need them. By harnessing technology we simplify small business operational processes providing valuable time and information for small business owners to grow their business. In the logo (bluvoria) we want to be able to see bluv and experts. The final design should communicate achieving growth dreams and balance (ie life and $).
Updates
This project has been temporarily placed on hold until I finalize "Tech Savy small Business accountant needs a logo". I invite all designers to submit on this logo project. Once my logo is finalized I will resume this business card contest. Thanks Added Wednesday, March 19, 2014
This project has been temporarily placed on hold until I finalize "Tech Savy small Business accountant logo". I invite all designers to submit on this logo project. Once my logo is finalized I will resume this business card contest. Thanks Added Thursday, March 20, 2014
Target Market(s)
Small Business (Revenue $500,000, more than 3 employees) owners.
Industry/Entity Type
Small Business
Contact Information for Business Card
Marcy Elwind (Principal)
Accountant, Tax Agent.
TEL | 0417 683 912
EMAIL | Marcy.Elwind@bluvoria.com.au
WEB | www.bluvoria.com.au
Look and feel

```html
<!DOCTYPE html>
<html lang="en">
<head>
<meta charset="utf-8">
<title>bluvoria business card</title>
<link rel="stylesheet" href="https://fonts.googleapis.com/css2?family=Poppins:wght@400;500;600&display=swap">
<style>
  :root {
    --bg: #e6e3de;
    --card-white: #ffffff;
    --card-back-light: #f4f4f4;
    --card-back-dark: #dcdcdc;
    --band-grey: #a3a5a8;
    --band-grey-dark: #8e9094;
    --brand-blue: #1ea8dc;
    --text-grey: #7d8084;
    --logo-grey: #8b8d91;
  }
  * { box-sizing: border-box; margin: 0; padding: 0; }
  html, body {
    width: 1200px; height: 780px; overflow: hidden;
    background: var(--bg);
    font-family: "Poppins", sans-serif;
  }
  .canvas {
    position: relative; width: 1200px; height: 780px;
    display: flex; align-items: center; justify-content: center; gap: 40px;
  }
  .card {
    position: relative; width: 520px; height: 297px; overflow: hidden;
    border-radius: 3px;
    box-shadow: 0 2px 6px rgba(0,0,0,0.12);
  }

  /* Front */
  .card-front { background: var(--card-white); }
  .card-front .swoosh { position: absolute; inset: 0; width: 100%; height: 100%; }
  .card-front .details {
    position: absolute; top: 30px; right: 28px;
    display: flex; flex-direction: column; align-items: flex-end;
    text-align: right;
  }
  .brand-name {
    color: var(--brand-blue); font-weight: 600;
    font-size: 44px; line-height: 1; letter-spacing: -1px;
  }
  .tagline { color: var(--text-grey); font-size: 13px; margin-top: 4px; }
  .person-name {
    color: var(--brand-blue); font-weight: 600;
    font-size: 23px; line-height: 1.1; margin-top: 20px;
  }
  .person-role { color: var(--text-grey); font-size: 13px; line-height: 1.35; }
  .contact-list { list-style: none; margin-top: 10px; }
  .contact-item {
    display: flex; align-items: center; justify-content: flex-end; gap: 8px;
    color: var(--text-grey); font-size: 13px; line-height: 1.6;
  }
  .contact-item.phone { font-size: 15px; }
  .icon { width: 16px; height: 16px; flex: none; }

  /* Back */
  .card-back {
    background: linear-gradient(135deg, var(--card-back-light) 0%, var(--card-back-dark) 100%);
    display: flex; align-items: center; justify-content: center;
  }
  .back-lockup { display: flex; flex-direction: column; align-items: flex-start; }
  .back-lockup .brand-name { font-size: 74px; color: var(--logo-grey); letter-spacing: -2px; }
  .back-lockup .tagline { font-size: 19px; margin-top: 6px; margin-left: 4px; }
</style>
</head>
<body>
<main class="canvas">
  <section class="card card-front" aria-label="Business card front">
    <svg class="swoosh" viewBox="0 0 520 297" preserveAspectRatio="none" aria-hidden="true">
      <path d="M0,0 L78,0 Q96,205 236,297 L0,297 Z" fill="var(--band-grey)"/>
      <path d="M93,0 Q113,198 256,297" fill="none" stroke="var(--brand-blue)" stroke-width="4"/>
    </svg>
    <div class="details">
      <div class="brand-name">bluvoria</div>
      <div class="tagline">Your business and accounting partner</div>
      <div class="person-name">Marcy Elwind</div>
      <div class="person-role">(Principal)</div>
      <div class="person-role">Accountant, Tax Agent</div>
      <ul class="contact-list">
        <li class="contact-item phone">0417 683 912
          <svg class="icon" viewBox="0 0 16 16" aria-hidden="true">
            <rect width="16" height="16" rx="2" fill="var(--brand-blue)"/>
            <path d="M5 3.5 L6.8 5.6 L5.8 7 Q7 9.2 9 10.2 L10.4 9.2 L12.5 11 L11.3 12.6 Q7 12.5 3.6 5 Z" fill="#fff"/>
          </svg>
        </li>
        <li class="contact-item">Marcy.Elwind@bluvoria.com.au
          <svg class="icon" viewBox="0 0 16 16" aria-hidden="true">
            <rect width="16" height="16" rx="2" fill="var(--brand-blue)"/>
            <rect x="3" y="4.5" width="10" height="7" fill="none" stroke="#fff" stroke-width="1.2"/>
            <path d="M3 4.5 L8 8.6 L13 4.5" fill="none" stroke="#fff" stroke-width="1.2"/>
          </svg>
        </li>
        <li class="contact-item">www.bluvoria.com.au
          <svg class="icon" viewBox="0 0 16 16" aria-hidden="true">
            <rect width="16" height="16" rx="2" fill="var(--brand-blue)"/>
            <circle cx="8" cy="8" r="4.8" fill="none" stroke="#fff" stroke-width="1.1"/>
            <ellipse cx="8" cy="8" rx="2" ry="4.8" fill="none" stroke="#fff" stroke-width="1"/>
            <path d="M3.2 8 H12.8" stroke="#fff" stroke-width="1"/>
          </svg>
        </li>
      </ul>
    </div>
  </section>

  <section class="card card-back" aria-label="Business card back">
    <div class="back-lockup">
      <div class="brand-name">bluvoria</div>
      <div class="tagline">Your business and accounting partner</div>
    </div>
  </section>
</main>
</body>
</html>
```